Poster for Kirtan Music Event

Design (3) 24" x 36" Posters

I have provided a sample a friend did in Australia: ( Picture No. 4 )

Use all the text on sample poster except the replacement changes below.

Replace with the following text as this is for different location:
Replacement Text:

Every Friday Night 7:00pm-8:30pm
Kealoha Pilates & Movement Studio
947 Hollister Rd Paia

Free Kirtan Experience! or Free Event
Mohan Priya Sevi & Companions

Optional Text:

A evening of music, singing of spiritual mantras, and refreshments

Bring flowers, musical instruments, friends, or just come with an open heart.

Meditate on transcendental sounds that provide rest for the mind & heart"

An evening of music & singing of sacred mantra's

```html
<!DOCTYPE html>
<html lang="en">
<head>
<meta charset="utf-8">
<title>Kirtan Experience — Music Event Poster</title>
<link rel="stylesheet" href="https://fonts.googleapis.com/css2?family=Anton&family=Almendra+SC&family=Federo&family=Arimo:ital,wght@1,700&display=swap">
<style>
  :root {
    --frame: #f3eeee;
    --red-deep: #7d1f24;
    --red: #a8323a;
    --red-mid: #c1453f;
    --orange: #e07a3a;
    --glow: #f5b25e;
    --band-light: rgba(255, 235, 225, 0.55);
    --title-red: #b0222c;
    --white: #ffffff;
    --green: #a4b62a;
    --amber: #e0852e;
    --badge: #5a1a1e;
  }
  * { box-sizing: border-box; margin: 0; padding: 0; }
  html, body { width: 800px; height: 1200px; overflow: hidden; background: var(--frame); }
  .poster {
    position: absolute; left: 10px; top: 10px; width: 780px; height: 1180px; overflow: hidden;
    background:
      radial-gradient(circle at 50% 47%, var(--glow) 0%, var(--orange) 22%, var(--red-mid) 48%, var(--red) 75%, var(--red-deep) 100%);
  }
  .mandala {
    position: absolute; left: 10px; top: 162px; width: 760px; height: 760px; border-radius: 50%;
    background: radial-gradient(circle, rgba(250,190,110,0.8) 0%, rgba(230,130,70,0.55) 45%, rgba(180,50,50,0.35) 75%, rgba(160,40,45,0) 100%);
  }
  .label {
    position: absolute; left: 252px; top: 12px; width: 276px; height: 98px;
    background: rgba(110, 30, 35, 0.55);
    display: flex; align-items: center; justify-content: center;
    font-family: "Anton", sans-serif; font-size: 36px; color: var(--white); letter-spacing: 0.5px;
    text-shadow: 0 0 8px rgba(255,255,255,0.6);
  }
  .title-band {
    position: absolute; left: 0; top: 132px; width: 780px; height: 124px;
    background: linear-gradient(180deg, #9c6a6c 0%, #7a4448 50%, #8e5a5d 100%);
    border-top: 2px solid rgba(255,255,255,0.35); border-bottom: 2px solid rgba(255,255,255,0.35);
    display: flex; align-items: center; justify-content: center;
  }
  .title {
    font-family: "Anton", sans-serif; font-size: 92px; line-height: 1; color: var(--white);
    letter-spacing: 1px; -webkit-text-stroke: 3px var(--title-red); paint-order: stroke fill;
    text-shadow: 3px 3px 0 var(--title-red);
  }
  .photo { position: absolute; }
  .photo--lead {
    left: 14px; top: 296px; width: 372px; height: 258px;
    background: radial-gradient(ellipse at 60% 45%, #e7a787 0%, #c96a5a 55%, rgba(170,60,60,0) 100%);
  }
  .photo--harmonium {
    left: 470px; top: 698px; width: 298px; height: 300px;
    background: radial-gradient(ellipse at 55% 50%, #e59a8c 0%, #bb5a5a 55%, rgba(160,50,55,0) 100%);
  }
  .badge {
    position: absolute; left: 576px; top: 333px; width: 120px; height: 120px; border-radius: 50%;
    background: var(--badge); color: var(--white); text-align: center;
    display: flex; flex-direction: column; justify-content: center;
    font-family: "Anton", sans-serif;
  }
  .badge__big { font-size: 42px; line-height: 1; }
  .badge__small { font-size: 22px; line-height: 1.1; }
  .schedule {
    position: absolute; left: 0; top: 538px; width: 780px; height: 118px;
    background: linear-gradient(90deg, rgba(255,235,225,0.3), var(--band-light) 30%, var(--band-light) 70%, rgba(255,235,225,0.3));
    display: flex; align-items: center; justify-content: center;
  }
  .schedule__text {
    font-family: "Almendra SC", serif; font-weight: 700; font-size: 48px; color: var(--title-red);
    text-shadow: 1px 1px 0 rgba(255,255,255,0.5);
  }
  .stars { position: absolute; left: 360px; width: 60px; height: 12px; }
  .stars--top { top: 548px; }
  .stars--bottom { top: 634px; }
  .note {
    position: absolute; width: 252px; height: 132px; padding: 20px 20px 0 18px;
    border: 3px solid rgba(255,255,255,0.8); border-radius: 6px 48px 6px 48px;
    font-family: "Arimo", sans-serif; font-style: italic; font-weight: 700; font-size: 16px; line-height: 1.25; color: var(--white);
  }
  .note--green { left: 44px; top: 716px; background: var(--green); }
  .note--amber { left: 220px; top: 862px; background: var(--amber); padding: 34px 20px 0 40px; }
  .footer { position: absolute; left: 0; top: 1024px; width: 780px; text-align: center; color: var(--white); }
  .footer__rule { display: block; margin: 0 auto; }
  .footer__line { font-family: "Federo", sans-serif; font-size: 25px; line-height: 42px; }
</style>
</head>
<body>
<main class="poster">
  <div class="mandala" role="img" aria-label="Large lotus mandala with radiating sunburst behind the poster content"></div>

  <div class="label">MUSIC EVENT</div>

  <div class="title-band"><h1 class="title">KIRTAN EXPERIENCE</h1></div>

  <div class="photo photo--lead" role="img" aria-label="Photo of a male musician singing into a microphone while playing guitar"></div>

  <div class="badge"><span class="badge__big">FREE</span><span class="badge__small">EVENT!</span></div>

  <div class="schedule"><p class="schedule__text">Every Friday Night 7:00pm-8:30pm</p></div>
  <svg class="stars stars--top" viewBox="0 0 60 12"><g fill="#b0222c"><polygon points="10,1 12,5 16,5 13,8 14,12 10,9.5 6,12 7,8 4,5 8,5"/><polygon points="30,1 32,5 36,5 33,8 34,12 30,9.5 26,12 27,8 24,5 28,5"/><polygon points="50,1 52,5 56,5 53,8 54,12 50,9.5 46,12 47,8 44,5 48,5"/></g></svg>
  <svg class="stars stars--bottom" viewBox="0 0 60 12"><g fill="#b0222c"><polygon points="10,1 12,5 16,5 13,8 14,12 10,9.5 6,12 7,8 4,5 8,5"/><polygon points="30,1 32,5 36,5 33,8 34,12 30,9.5 26,12 27,8 24,5 28,5"/><polygon points="50,1 52,5 56,5 53,8 54,12 50,9.5 46,12 47,8 44,5 48,5"/></g></svg>

  <p class="note note--green">Join us in the singing of transcendental sounds that provide rest for the mind &amp; heart</p>
  <p class="note note--amber">An evening of music &amp; singing of sacred mantra's</p>

  <div class="photo photo--harmonium" role="img" aria-label="Photo of a female musician singing while playing a harmonium"></div>

  <footer class="footer">
    <svg class="footer__rule" width="220" height="28" viewBox="0 0 220 28">
      <polygon fill="#ffffff" points="110,1 113,8 120,8 114.5,12.5 117,20 110,15.5 103,20 105.5,12.5 100,8 107,8"/>
      <line x1="0" y1="26" x2="220" y2="26" stroke="#ffffff" stroke-width="2"/>
    </svg>
    <p class="footer__line">Kealoha Pilates &amp; Movement Studio</p>
    <p class="footer__line">947 Hollister Rd Paia</p>
  </footer>
</main>
</body>
</html>
```